Thank You Card Design for Personal Injury Law Firm

Hi -
I am interested in getting a design for a thank you card that captures my law firm's brand. I am providing a drop box link to a folder that contains pictures of the firm's staff and some happy clients. The dropbox folder will also include a folder that we mail to prospective clients. You may want to use pictures from it in addition to or in place of staff and client pictures. https://www.filquorra.net/sh/pelv3kx7tumwq2b/ZTRNLbcHoWEqJFm42tixpRk8y?dl=0

Target Market(s)

Adult males and females who have been in car accidents

Industry/Entity Type

Legal

Requirements
Nice to have
• Want it to have a happy, cheerful feel. But it must also be professional.

```html
<!DOCTYPE html>
<html lang="en">
<head>
<meta charset="utf-8">
<title>Harlow Law Group – Thank You Card</title>
<link rel="stylesheet" href="https://fonts.googleapis.com/css2?family=Montserrat:wght@500;600;700;800&display=swap">
<style>
  :root {
    --navy: #004b7c;
    --navy-deep: #00436f;
    --rule: #4f7fae;
    --ink: #0a4a7a;
    --paper: #ffffff;
    --backdrop: #e4e4e4;
  }
  * { box-sizing: border-box; margin: 0; padding: 0; }
  html, body { width: 1029px; height: 1200px; overflow: hidden; }
  body {
    background: var(--backdrop);
    font-family: "Montserrat", Arial, sans-serif;
    position: relative;
  }
  .card {
    position: absolute;
    left: 64px; top: 100px;
    width: 900px; height: 1000px;
    box-shadow: 0 6px 18px rgba(0,0,0,.18);
  }
  .card-back {
    height: 500px;
    background: linear-gradient(var(--navy), var(--navy-deep));
    position: relative;
  }
  .back-url {
    position: absolute;
    top: 48px; left: 0; right: 0;
    text-align: center;
    color: var(--paper);
    font-size: 11px;
    font-weight: 700;
    letter-spacing: .3px;
    transform: rotate(180deg);
  }
  .card-front {
    height: 500px;
    background: var(--paper);
    position: relative;
  }
  .frame {
    position: absolute;
    left: 60px; top: 32px;
    width: 780px; height: 420px;
    border: 1.5px solid var(--rule);
  }
  .frame-divider {
    position: absolute;
    left: 0; right: 0;
    border-top: 1.5px solid var(--rule);
  }
  .frame-divider.upper { top: 112px; }
  .frame-divider.lower { top: 302px; }
  .photo-strip {
    position: absolute;
    display: flex;
    gap: 2px;
  }
  .photo {
    width: 108px; height: 78px;
  }
  .strip-top-left { left: 25px; top: 20px; }
  .strip-top-right { left: 421px; top: 20px; }
  .strip-bottom-left { left: 35px; top: 322px; }
  .strip-bottom-right { left: 421px; top: 322px; }
  .tone-office { background: linear-gradient(135deg, #d8c9a8, #3f5c8f 60%, #7a5a3f); }
  .tone-portrait { background: linear-gradient(135deg, #e9eef2, #e8c9b8 55%, #f3e6e4); }
  .tone-street { background: linear-gradient(135deg, #c9d9e8, #1f3352 55%, #e9edf0); }
  .tone-family { background: linear-gradient(135deg, #2f5f86, #5fa6d6 55%, #c9a486); }
  .tone-desk { background: linear-gradient(135deg, #8a3a2c, #2a2a2e 55%, #d7b59a); }
  .tone-garden { background: linear-gradient(135deg, #dfe4e2, #6d8a5a 55%, #34466b); }
  .tone-interior { background: linear-gradient(135deg, #efe6e2, #c7364a 60%, #5c3f7a); }
  .tone-table { background: linear-gradient(135deg, #f1efe9, #1f3f7a 55%, #b24a2a); }
  .tone-park { background: linear-gradient(135deg, #8fb07a, #3b4a3a 55%, #c9cdb8); }
  .tone-handshake { background: linear-gradient(135deg, #b9cfa8, #3d6fa8 55%, #6b7c4e); }
  .tone-smile { background: linear-gradient(135deg, #cfd6dc, #f2f2f0 50%, #5d4534); }
  .tone-couple { background: linear-gradient(135deg, #a9c49a, #2c3550 55%, #dfe3e8); }
  .brand-block {
    position: absolute;
    left: 70px; top: 128px;
    width: 330px;
    text-align: center;
    color: var(--ink);
  }
  .brand-name {
    display: flex;
    align-items: center;
    justify-content: center;
    gap: 10px;
    height: 78px;
    font-size: 27px;
    font-weight: 600;
    letter-spacing: 1px;
    color: var(--navy);
  }
  .brand-square {
    width: 48px; height: 48px;
    background: var(--navy);
    flex: none;
  }
  .phone {
    margin-top: 22px;
    font-size: 23px;
    font-weight: 700;
    letter-spacing: .5px;
  }
  .address, .web {
    font-size: 13px;
    font-weight: 600;
    margin-top: 4px;
  }
  .web { margin-top: 7px; }
  .greeting {
    position: absolute;
    left: 440px; top: 140px;
    width: 300px;
    text-align: center;
    color: var(--navy);
    font-weight: 800;
    font-size: 58px;
    line-height: 64px;
  }
</style>
</head>
<body>
  <div class="card">
    <section class="card-back">
      <p class="back-url">www.harlowlaw.com</p>
    </section>

    <section class="card-front">
      <div class="frame">
        <div class="frame-divider upper"></div>
        <div class="frame-divider lower"></div>

        <div class="photo-strip strip-top-left">
          <div class="photo tone-office" role="img" aria-label="Attorney smiling at his office desk"></div>
          <div class="photo tone-portrait" role="img" aria-label="Staff member standing by the firm's office sign"></div>
          <div class="photo tone-street" role="img" aria-label="Two attorneys in suits standing outside"></div>
        </div>
        <div class="photo-strip strip-top-right">
          <div class="photo tone-family" role="img" aria-label="Happy client family holding a baby"></div>
          <div class="photo tone-desk" role="img" aria-label="Attorney in a vest seated at a desk"></div>
          <div class="photo tone-garden" role="img" aria-label="Two staff members standing outdoors"></div>
        </div>

        <div class="brand-block">
          <div class="brand-name"><span class="brand-square"></span><span>HARLOW LAW GROUP</span></div>
          <p class="phone">907 555 0142</p>
          <p class="address">218 Birch Street • Kenai Bay, AK 99620</p>
          <p class="web">www.harlowlaw.com</p>
        </div>

        <h1 class="greeting">Thank<br>You</h1>

        <div class="photo-strip strip-bottom-left">
          <div class="photo tone-interior" role="img" aria-label="Staff member seated in a lobby"></div>
          <div class="photo tone-table" role="img" aria-label="Smiling staff member at a table"></div>
          <div class="photo tone-park" role="img" aria-label="Staff member smiling outdoors"></div>
        </div>
        <div class="photo-strip strip-bottom-right">
          <div class="photo tone-handshake" role="img" aria-label="Attorney shaking hands with a client"></div>
          <div class="photo tone-smile" role="img" aria-label="Smiling client at home"></div>
          <div class="photo tone-couple" role="img" aria-label="Happy client couple outdoors"></div>
        </div>
      </div>
    </section>
  </div>
</body>
</html>
```